Business card for start up company

SIMPLE, CLEAN, FRESH, MODERN, SOPHISTICATED. professional. experienced, easy to deal with, expert in the field. local ethics.

professional business card for Forge Mark Works. using company logo supplied and images.

GENERAL ENGINEERING - MACHINING - WELDING - MAINTENANCE

Forge Mark Works Ltd is a locally owned mechanical engineering company that specialises in general and mechanical engineering, as well as steel fabrication, welding, repairs and maintenance.

We specialise in the design, welding, fabrication and installation of stainless and mild steel fabrications. We service commercial and residential clients; large or small projects; production line or one off designs.

We have built a solid reputation for quality and service for our machinery and engineering work around Northland NZ. For innovative, cost effective and efficient engineering solutions, to suit a wide range of commercial, residential and rural applications.

Reason: doing on behalf. went away on holiday

Target Market(s)

boat builders. DIY. industrial. RESIDENTIAL. COMMERCIAL

Industry/Entity Type

Mechanical Engineering

Contact Information for Business Card

CONTACT / SERVICES SIDE
Forge Mark Works Ltd.
Design | Machining | Welding | Fabrication | Installation | Maintenance
www.forgemarkworks-example.co.nz
grant@forgemarkworks-example.co.nz

Font styles to use
Serif

Colors

Designer to choose colors to be used in the design.

Requirements
Must have
• LOGO ONLY WITH NEGATIVE SPACE ON FRONT SIDE
• services and contact side , either use stock photos (supplied) as background or background supplied in logo photos.
Nice to have
• use the symbol icon in logo on contact/ services side, , enlarged, transparent and faded into the background with text over the top on the
• Design | Machining | Welding | Fabrication | Installation | Maintenance
• the above services to be subtle, along the bottom edge of the services side. can i also have another proof with eh above services featuring on the bottom edge of the LOGO FRONT side to see if the text looks better with or without.
Should not have
• crowded, busy, different fonts. different casing.
• use fonts in the logo files designer to make font decision.

```html
<!DOCTYPE html>
<html lang="en">
<head>
<meta charset="utf-8">
<title>Forge Mark Works – Business Card</title>
<link rel="stylesheet" href="https://fonts.googleapis.com/css2?family=Roboto:wght@300;400;500;700&display=swap">
<style>
  :root{
    --page:#e3e3e3;
    --card-dark:#121212;
    --card-mid:#2c2c2c;
    --card-light:#454545;
    --type-light:#e6e6e6;
    --type-soft:#cfcfcf;
    --accent:#e0582a;
  }
  *{box-sizing:border-box;margin:0;padding:0}
  html,body{width:1200px;height:1200px;overflow:hidden}
  body{background:var(--page);font-family:"Roboto",Arial,sans-serif;position:relative}

  .card{position:absolute;left:130px;width:940px;height:534px;overflow:hidden;
        box-shadow:0 10px 24px rgba(0,0,0,.35)}
  .card--front{top:40px}
  .card--back{top:626px}

  .card__photo{position:absolute;inset:0}
  .card--front .card__photo{
    background:
      radial-gradient(ellipse 55% 60% at 62% 38%, #3a3a3a 0%, rgba(40,40,40,0) 70%),
      linear-gradient(180deg,var(--card-dark) 0%,var(--card-mid) 65%,var(--card-light) 100%);
  }
  .card--back .card__photo{
    background:
      linear-gradient(150deg,var(--card-dark) 0%,#1c1c1c 40%,#383838 62%,#161616 82%,#0c0c0c 100%);
  }

  .brand{position:absolute;left:0;right:0;display:flex;align-items:center;justify-content:center;gap:16px;
         color:var(--type-light);font-weight:500;text-transform:uppercase;letter-spacing:.5px}
  .brand__square{width:16px;height:16px;background:var(--accent)}
  .card--front .brand{top:250px;font-size:50px}
  .card--back .brand{top:150px;font-size:44px}

  .services{position:absolute;left:0;right:0;text-align:center;font-weight:300;font-size:24px;color:#f2f2f2;white-space:nowrap}
  .card--front .services{top:408px}

  .company{position:absolute;left:0;right:0;top:290px;text-align:center;font-weight:700;font-size:30px;color:var(--type-soft)}

  .contact{position:absolute;left:0;right:0;top:362px;display:flex;justify-content:center;gap:56px;
           font-size:23px;font-weight:300;color:#f0f0f0}
  .contact__item{display:flex;align-items:center;gap:10px}
  .contact__icon{width:26px;height:26px;flex:none}

  .services-band{position:absolute;left:0;right:0;top:430px;height:48px;background:var(--accent);
                 display:flex;align-items:center;justify-content:center}
  .services-band .services{position:static;color:#fff4ec}
</style>
</head>
<body>

  <section class="card card--front">
    <div class="card__photo" role="img" aria-label="Dark close-up photograph of machined steel gears and threaded parts"></div>
    <div class="brand"><span class="brand__square"></span>Forge Mark Works</div>
    <p class="services">Design | Machining | Welding | Fabrication | Installation | Maintenance</p>
  </section>

  <section class="card card--back">
    <div class="card__photo" role="img" aria-label="Dark close-up photograph of a threaded steel shaft"></div>
    <div class="brand"><span class="brand__square"></span>Forge Mark Works</div>
    <p class="company">Forge Mark Works Ltd.</p>
    <div class="contact">
      <span class="contact__item">
        <svg class="contact__icon" viewBox="0 0 26 26" aria-hidden="true">
          <text x="13" y="21" text-anchor="middle" font-family="Roboto,Arial,sans-serif" font-size="26" font-style="italic" fill="#e0582a">@</text>
        </svg>
        grant@forgemarkworks-example.co.nz
      </span>
      <span class="contact__item">
        <svg class="contact__icon" viewBox="0 0 26 26" aria-hidden="true" fill="none" stroke="#e0582a" stroke-width="1.4">
          <circle cx="13" cy="13" r="11"/>
          <ellipse cx="13" cy="13" rx="5" ry="11"/>
          <line x1="2" y1="13" x2="24" y2="13"/>
          <path d="M4 7.5h18M4 18.5h18"/>
        </svg>
        www.forgemarkworks-example.co.nz
      </span>
    </div>
    <div class="services-band">
      <p class="services">Design | Machining | Welding | Fabrication | Installation | Maintenance</p>
    </div>
  </section>

</body>
</html>
```